Sonic Vale

Rebrand current website and move it to SonicVale.com. Looking for a professional, eye catching, top 10 in World type website. My current website is: https://madebytorven.sitepadhub.com/sonicvale
I would like it moved to sonicvale.com.

```html
<!DOCTYPE html>
<html lang="en">
<head>
<meta charset="utf-8">
<title>Sonic Vale</title>
<link href="https://fonts.googleapis.com/css2?family=Oswald:wght@400;500;600&family=Roboto:wght@400;500&display=swap" rel="stylesheet">
<style>
:root{
  --bg:#141414;
  --red:#e5141c;
  --red-dark:#a30d12;
  --white:#ffffff;
  --muted:#bdbdbd;
  --field:#202020;
}
*{margin:0;padding:0;box-sizing:border-box}
html,body{width:1200px;height:4389px;overflow:hidden;background:var(--bg);color:var(--white);font-family:"Roboto",sans-serif}
.page{position:relative;width:1200px;height:4389px;background:linear-gradient(180deg,#181818 0,#121212 100%)}
.abs{position:absolute}

/* hero */
.hero{position:absolute;left:0;top:0;width:1200px;height:627px;background:linear-gradient(90deg,#0d0d0d 0,#1a1a1a 45%,#2a2a2a 100%)}
.hero-photo{position:absolute;right:0;top:0;width:640px;height:627px;background:radial-gradient(ellipse at 60% 40%,#5a5a5a 0,#2c2c2c 55%,#121212 100%)}
.logo{position:absolute;left:111px;top:50px;font-family:"Oswald",sans-serif;font-weight:600;font-size:24px;line-height:30px;color:var(--red);letter-spacing:1px}
.nav a{color:var(--white);text-decoration:none;position:absolute;top:32px;white-space:nowrap;font-family:"Oswald",sans-serif;font-size:17px;line-height:24px}
.nav a.active{color:var(--red)}
.social{position:absolute;left:50px;width:12px;height:12px;border-radius:50%;background:var(--white)}
.follow{position:absolute;left:47px;top:430px;transform:rotate(-90deg);transform-origin:left top;font-family:"Oswald",sans-serif;font-size:12px;line-height:14px;letter-spacing:2px}
.follow-line{position:absolute;left:56px;top:316px;width:1px;height:42px;background:var(--red)}
.hero-kicker{left:140px;top:236px;font-family:"Oswald",sans-serif;font-size:14px;line-height:18px;letter-spacing:1px}
.hero-title{left:138px;top:266px;font-family:"Oswald",sans-serif;font-weight:500;font-size:54px;line-height:57px;letter-spacing:4px}
.hero-title .red{color:var(--red)}
.play{left:140px;top:406px;display:flex;align-items:center;gap:18px;font-family:"Oswald",sans-serif;font-size:15px}
.slides{position:absolute;left:1126px;top:232px;font-family:"Oswald",sans-serif;font-size:13px;line-height:16px;text-align:center;width:16px}
.slides span{display:block;height:48px}
.slides .on{color:var(--red)}

/* section heads */
.kicker{position:absolute;left:0;width:1200px;text-align:center;font-family:"Oswald",sans-serif;font-size:20px;line-height:26px;letter-spacing:2px}
.big-title{position:absolute;left:0;width:1200px;text-align:center;font-family:"Oswald",sans-serif;font-weight:500;font-size:56px;line-height:62px;letter-spacing:17px;color:var(--red);padding-left:17px}
.rule{position:absolute;left:563px;width:74px;height:2px;background:var(--white)}

.about-photo{left:174px;top:839px;width:852px;height:511px;background:linear-gradient(135deg,#8a8a8a 0,#4d4d4d 45%,#262626 100%)}
.about-text{left:160px;top:1368px;width:880px;text-align:center;font-size:16px;line-height:33.5px;color:var(--muted)}

.mix-title{left:111px;top:1537px;font-family:"Oswald",sans-serif;font-size:20px;line-height:26px;letter-spacing:2px}
.mix-sub{left:111px;top:1570px;font-size:14px;line-height:18px}
.mix-arrow{left:112px;top:1604px}

.player{position:absolute;width:310px;height:75px;background:var(--red-dark)}
.player .bar{position:absolute;left:0;top:0;width:310px;height:26px;background:var(--red);font-size:14px;line-height:16px;padding:5px 9px}
.player .wave{position:absolute;left:42px;top:36px;width:210px;height:30px;background:linear-gradient(180deg,transparent 30%,#d9423f 50%,transparent 70%);opacity:.8}
.player .pause{position:absolute;left:14px;top:42px}
.player .power{position:absolute;right:0;top:26px;width:52px;height:49px;background:var(--red);display:flex;align-items:center;justify-content:center}
.player .tools{position:absolute;right:8px;top:6px}

.quote-band{left:0;top:2012px;width:1200px;height:366px;background:radial-gradient(ellipse at 50% 50%,#3a3a3a 0,#1e1e1e 60%,#141414 100%)}
.quote{left:0;top:2105px;width:1200px;text-align:center;font-family:"Oswald",sans-serif;font-size:29px;line-height:46px}
.quote-author{left:0;top:2220px;width:1200px;text-align:center;font-size:20px;line-height:26px;color:#dcdcdc}

.learn-title{left:116px;top:2470px;font-family:"Oswald",sans-serif;font-weight:500;font-size:29px;line-height:35px;letter-spacing:3px}
.learn-text{left:116px;top:2550px;width:230px;font-size:15px;line-height:23px;color:#d0d0d0}
.btn-more{left:112px;top:2665px;width:209px;height:41px;border-radius:21px;background:var(--red);font-family:"Oswald",sans-serif;font-size:15px;display:flex;align-items:center;justify-content:center}
.card{position:absolute;top:2472px;width:232px}
.card .img{width:232px;height:159px;background:linear-gradient(135deg,#7a7a7a,#2a2a2a)}
.card .meta{margin-top:14px;font-size:11px;line-height:14px}
.card .title{margin-top:6px;font-family:"Oswald",sans-serif;font-size:16px;line-height:20px}
.card .more{margin-top:8px;font-size:12px;line-height:15px;color:var(--red);text-decoration:underline}

.map{left:111px;top:2975px;width:978px;height:426px;background:linear-gradient(135deg,#9c9c9c,#b8b8b8 50%,#8f8f8f)}

.touch{left:0;top:3487px;width:1200px;text-align:center;font-family:"Oswald",sans-serif;font-weight:400;font-size:29px;line-height:38px;letter-spacing:3px}
.touch-sub{left:0;top:3550px;width:1200px;text-align:center;font-family:"Oswald",sans-serif;font-size:15px;line-height:30px;letter-spacing:2px}
.label{position:absolute;font-family:"Oswald",sans-serif;font-size:18px;line-height:24px;letter-spacing:1px}
.field{position:absolute;background:var(--field);font-size:13px;line-height:16px;color:#8a8a8a;padding:16px 18px}
.submit{left:189px;top:4049px;width:820px;height:62px;background:var(--red);font-family:"Oswald",sans-serif;font-size:22px;display:flex;align-items:center;justify-content:center}

.contact-item{position:absolute;top:4186px;display:flex;gap:14px;align-items:flex-start}
.contact-item h4{font-family:"Oswald",sans-serif;font-weight:500;font-size:22px;letter-spacing:4px;line-height:26px}
.contact-item p{font-family:"Oswald",sans-serif;font-size:14px;line-height:18px;color:var(--red)}
.copyright{left:0;top:4345px;width:1200px;text-align:center;font-size:14px;line-height:18px}
</style>
</head>
<body>
<div class="page">

  <header class="hero">
    <div class="hero-photo" role="img" aria-label="Black and white portrait of a singer in mirrored sunglasses"></div>
    <div class="logo">SONIC VALE</div>
    <nav class="nav">
      <a class="active" style="left:413px">HOME</a>
      <a style="left:510px">ABOUT</a>
      <a style="left:613px">MUSIC</a>
      <a style="left:713px">LYRICS</a>
      <a style="left:817px">SHOP</a>
      <a style="left:913px">BLOG</a>
      <a style="left:1007px">CONTACT US</a>
    </nav>
    <span class="social" style="top:234px"></span>
    <span class="social" style="top:267px"></span>
    <span class="social" style="top:301px"></span>
    <div class="follow-line"></div>
    <div class="follow">FOLLOW</div>

    <div class="abs hero-kicker">THE LYRICS REVOLVE A ROUND LOVE</div>
    <h1 class="abs hero-title">JOURNEY WITH<br><span class="red">TORVEN ASHCROFT</span></h1>
    <div class="abs play">
      <svg width="44" height="44" viewBox="0 0 44 44"><circle cx="22" cy="22" r="20.5" fill="none" stroke="#fff" stroke-width="1.5"/><path d="M18 15 L29 22 L18 29Z" fill="#e5141c"/></svg>
      PLAY MUSIC
    </div>
    <div class="slides">
      <span>01<br>|</span><span class="on">02<br>|</span><span>03<br>|</span><span>04</span>
    </div>
  </header>

  <div class="kicker" style="top:708px">A LIFE STEEPED IN SOUND</div>
  <h2 class="big-title" style="top:740px">ABOUT ME</h2>
  <div class="rule" style="top:810px"></div>
  <div class="abs about-photo" role="img" aria-label="Black and white photo of the artist in his studio"></div>
  <p class="abs about-text">Hailing from New Orleans, Torven has always pushed himself to achieve more success in his music career. Looking to perfect his technical abilities and develop his own unique style, Torven draws upon his New Orleans roots and lifelong passion for music. Get in touch to learn more about his background, experience, and latest projects.</p>

  <div class="abs mix-title">MIXING AND MASTERING</div>
  <div class="abs mix-sub">Music Producer Portfolio</div>
  <svg class="abs mix-arrow" width="20" height="26" viewBox="0 0 20 26"><path d="M10 2 V22 M2 14 L10 22 L18 14" fill="none" stroke="#e5141c" stroke-width="2"/></svg>

  <div class="player" style="left:111px;top:1649px"><div class="bar">Night Shift Demo</div><svg class="tools" width="30" height="14"><path d="M1 5h3l4-3v10l-4-3H1z" fill="#fff"/><circle cx="20" cy="7" r="2" fill="#fff"/><circle cx="27" cy="3" r="2" fill="#fff"/><circle cx="27" cy="11" r="2" fill="#fff"/><path d="M20 7 27 3M20 7 27 11" stroke="#fff"/></svg><svg class="pause" width="12" height="18"><rect width="4" height="18" fill="#fff"/><rect x="8" width="4" height="18" fill="#fff"/></svg><div class="wave"></div><div class="power"><svg width="24" height="24" viewBox="0 0 24 24"><path d="M7 6a8 8 0 1 0 10 0M12 2v9" fill="none" stroke="#fff" stroke-width="2.4" stroke-linecap="round"/></svg></div></div>
  <div class="player" style="left:445px;top:1649px"><div class="bar">Low End / Torven</div><svg class="tools" width="30" height="14"><path d="M1 5h3l4-3v10l-4-3H1z" fill="#fff"/><circle cx="20" cy="7" r="2" fill="#fff"/><circle cx="27" cy="3" r="2" fill="#fff"/><circle cx="27" cy="11" r="2" fill="#fff"/><path d="M20 7 27 3M20 7 27 11" stroke="#fff"/></svg><svg class="pause" width="12" height="18"><rect width="4" height="18" fill="#fff"/><rect x="8" width="4" height="18" fill="#fff"/></svg><div class="wave"></div><div class="power"><svg width="24" height="24" viewBox="0 0 24 24"><path d="M7 6a8 8 0 1 0 10 0M12 2v9" fill="none" stroke="#fff" stroke-width="2.4" stroke-linecap="round"/></svg></div></div>
  <div class="player" style="left:779px;top:1649px"><div class="bar">Signal / Torven</div><svg class="tools" width="30" height="14"><path d="M1 5h3l4-3v10l-4-3H1z" fill="#fff"/><circle cx="20" cy="7" r="2" fill="#fff"/><circle cx="27" cy="3" r="2" fill="#fff"/><circle cx="27" cy="11" r="2" fill="#fff"/><path d="M20 7 27 3M20 7 27 11" stroke="#fff"/></svg><svg class="pause" width="12" height="18"><rect width="4" height="18" fill="#fff"/><rect x="8" width="4" height="18" fill="#fff"/></svg><div class="wave"></div><div class="power"><svg width="24" height="24" viewBox="0 0 24 24"><path d="M7 6a8 8 0 1 0 10 0M12 2v9" fill="none" stroke="#fff" stroke-width="2.4" stroke-linecap="round"/></svg></div></div>

  <div class="player" style="left:111px;top:1746px"><div class="bar">Brass Line / Torven</div><svg class="tools" width="30" height="14"><path d="M1 5h3l4-3v10l-4-3H1z" fill="#fff"/><circle cx="20" cy="7" r="2" fill="#fff"/><circle cx="27" cy="3" r="2" fill="#fff"/><circle cx="27" cy="11" r="2" fill="#fff"/><path d="M20 7 27 3M20 7 27 11" stroke="#fff"/></svg><svg class="pause" width="12" height="18"><rect width="4" height="18" fill="#fff"/><rect x="8" width="4" height="18" fill="#fff"/></svg><div class="wave"></div><div class="power"><svg width="24" height="24" viewBox="0 0 24 24"><path d="M7 6a8 8 0 1 0 10 0M12 2v9" fill="none" stroke="#fff" stroke-width="2.4" stroke-linecap="round"/></svg></div></div>
  <div class="player" style="left:445px;top:1746px"><div class="bar">Late Run / Torven</div><svg class="tools" width="30" height="14"><path d="M1 5h3l4-3v10l-4-3H1z" fill="#fff"/><circle cx="20" cy="7" r="2" fill="#fff"/><circle cx="27" cy="3" r="2" fill="#fff"/><circle cx="27" cy="11" r="2" fill="#fff"/><path d="M20 7 27 3M20 7 27 11" stroke="#fff"/></svg><svg class="pause" width="12" height="18"><rect width="4" height="18" fill="#fff"/><rect x="8" width="4" height="18" fill="#fff"/></svg><div class="wave"></div><div class="power"><svg width="24" height="24" viewBox="0 0 24 24"><path d="M7 6a8 8 0 1 0 10 0M12 2v9" fill="none" stroke="#fff" stroke-width="2.4" stroke-linecap="round"/></svg></div></div>
  <div class="player" style="left:779px;top:1746px"><div class="bar">Velvet / Torven</div><svg class="tools" width="30" height="14"><path d="M1 5h3l4-3v10l-4-3H1z" fill="#fff"/><circle cx="20" cy="7" r="2" fill="#fff"/><circle cx="27" cy="3" r="2" fill="#fff"/><circle cx="27" cy="11" r="2" fill="#fff"/><path d="M20 7 27 3M20 7 27 11" stroke="#fff"/></svg><svg class="pause" width="12" height="18"><rect width="4" height="18" fill="#fff"/><rect x="8" width="4" height="18" fill="#fff"/></svg><div class="wave"></div><div class="power"><svg width="24" height="24" viewBox="0 0 24 24"><path d="M7 6a8 8 0 1 0 10 0M12 2v9" fill="none" stroke="#fff" stroke-width="2.4" stroke-linecap="round"/></svg></div></div>

  <div class="player" style="left:111px;top:1841px"><div class="bar">Slow Burn / Torven</div><svg class="tools" width="30" height="14"><path d="M1 5h3l4-3v10l-4-3H1z" fill="#fff"/><circle cx="20" cy="7" r="2" fill="#fff"/><circle cx="27" cy="3" r="2" fill="#fff"/><circle cx="27" cy="11" r="2" fill="#fff"/><path d="M20 7 27 3M20 7 27 11" stroke="#fff"/></svg><svg class="pause" width="12" height="18"><rect width="4" height="18" fill="#fff"/><rect x="8" width="4" height="18" fill="#fff"/></svg><div class="wave"></div><div class="power"><svg width="24" height="24" viewBox="0 0 24 24"><path d="M7 6a8 8 0 1 0 10 0M12 2v9" fill="none" stroke="#fff" stroke-width="2.4" stroke-linecap="round"/></svg></div></div>
  <div class="player" style="left:445px;top:1841px"><div class="bar">Harbor Lights / Torven</div><svg class="tools" width="30" height="14"><path d="M1 5h3l4-3v10l-4-3H1z" fill="#fff"/><circle cx="20" cy="7" r="2" fill="#fff"/><circle cx="27" cy="3" r="2" fill="#fff"/><circle cx="27" cy="11" r="2" fill="#fff"/><path d="M20 7 27 3M20 7 27 11" stroke="#fff"/></svg><svg class="pause" width="12" height="18"><rect width="4" height="18" fill="#fff"/><rect x="8" width="4" height="18" fill="#fff"/></svg><div class="wave"></div><div class="power"><svg width="24" height="24" viewBox="0 0 24 24"><path d="M7 6a8 8 0 1 0 10 0M12 2v9" fill="none" stroke="#fff" stroke-width="2.4" stroke-linecap="round"/></svg></div></div>
  <div class="player" style="left:779px;top:1841px"><div class="bar">Night Drive / Torven</div><svg class="tools" width="30" height="14"><path d="M1 5h3l4-3v10l-4-3H1z" fill="#fff"/><circle cx="20" cy="7" r="2" fill="#fff"/><circle cx="27" cy="3" r="2" fill="#fff"/><circle cx="27" cy="11" r="2" fill="#fff"/><path d="M20 7 27 3M20 7 27 11" stroke="#fff"/></svg><svg class="pause" width="12" height="18"><rect width="4" height="18" fill="#fff"/><rect x="8" width="4" height="18" fill="#fff"/></svg><div class="wave"></div><div class="power"><svg width="24" height="24" viewBox="0 0 24 24"><path d="M7 6a8 8 0 1 0 10 0M12 2v9" fill="none" stroke="#fff" stroke-width="2.4" stroke-linecap="round"/></svg></div></div>

  <div class="abs quote-band" role="img" aria-label="Dark close-up of a mixing console"></div>
  <blockquote class="abs quote">“Music expresses that which cannot be said and on<br>which it is impossible to be silent”</blockquote>
  <div class="abs quote-author">Elias Marlow</div>

  <h3 class="abs learn-title">LEARN FROM THE<br>MUSIC.</h3>
  <p class="abs learn-text">Sed ut perspiciatis unde omnis iste ts error sit voluptatemorem que laudantium, totam rem aperiam, eaque ipsa</p>
  <div class="abs btn-more">MORE BLOG</div>

  <article class="card" style="left:351px"><div class="img" role="img" aria-label="Guitarist playing on stage"></div><div class="meta">FEATURES 3 WEEKS AGO</div><div class="title">The standard Lorem Ipsum<br>passage, used the 1500</div><div class="more">Read More »</div></article>
  <article class="card" style="left:604px"><div class="img" role="img" aria-label="DJ mixer and headphones"></div><div class="meta">FEATURES 3 WEEKS AGO</div><div class="title">The standard Lorem Ipsum<br>passage, used the 1500</div><div class="more">Read More »</div></article>
  <article class="card" style="left:856px"><div class="img" role="img" aria-label="Band rehearsing in a studio"></div><div class="meta">FEATURES 3 WEEKS AGO</div><div class="title">The standard Lorem Ipsum<br>passage, used the 1500</div><div class="more">Read More »</div></article>

  <div class="kicker" style="top:2831px">A LIFE STEEPED IN SOUND</div>
  <h2 class="big-title" style="top:2862px">CONTACT US</h2>
  <div class="rule" style="top:2933px"></div>
  <div class="abs map" role="img" aria-label="Street map showing the studio location"></div>

  <h2 class="abs touch">GET IN TOUCH WITH US</h2>
  <p class="abs touch-sub">LOREM IPSUM DOLOR SIT AMET, CONSECTETUR ADIPISCING ELIT, SED<br>DO EIUSMOD TEMPOR INCIDIDUNT UT</p>

  <div class="label" style="left:191px;top:3642px">NAME</div>
  <div class="label" style="left:612px;top:3642px">PHONE</div>
  <div class="field" style="left:189px;top:3677px;width:401px;height:48px">Enter your name</div>
  <div class="field" style="left:612px;top:3677px;width:397px;height:48px">Enter your number</div>
  <div class="label" style="left:191px;top:3744px">EMAIL</div>
  <div class="field" style="left:189px;top:3780px;width:820px;height:48px">Enter email address</div>
  <div class="label" style="left:191px;top:3862px">COMMEND</div>
  <div class="field" style="left:189px;top:3898px;width:820px;height:126px">Type your message here</div>
  <div class="abs submit">SUBMIT</div>

  <div class="contact-item" style="left:345px">
    <svg width="50" height="46" viewBox="0 0 50 46"><path d="M3 18 L25 3 L47 18 V43 H3Z M3 18 L25 32 L47 18" fill="none" stroke="#e5141c" stroke-width="2"/><circle cx="25" cy="17" r="6" fill="none" stroke="#e5141c" stroke-width="2"/></svg>
    <div><h4>MAIL US AT</h4><p>HELLO@SONICVALE.COM</p></div>
  </div>
  <div class="contact-item" style="left:668px">
    <svg width="46" height="46" viewBox="0 0 46 46"><path d="M10 4 L17 13 L13 18 Q18 28 28 33 L33 29 L42 36 L37 43 Q18 42 4 12Z" fill="none" stroke="#e5141c" stroke-width="2"/><path d="M26 6 Q38 8 40 20 M26 12 Q32 13 34 20" fill="none" stroke="#e5141c" stroke-width="2"/></svg>
    <div><h4>CALL US AT</h4><p>404-555-0187</p></div>
  </div>

  <footer class="abs copyright">Copyright © 2021 Sonic Vale . All rights reserved.</footer>
</div>
</body>
</html>
```